Small Business Broker Business Card Design

A business card design for a small business brokerage, which is a financial service, not unlike real estate brokerage, but for small businesses such as laundromats, pizza shops, restaurants, cleaners etc. The designs should all be simple, more conservative in nature, using the colors and font of the logo. Again, think real estate Brokerage as a business context
Contact Information for Business Card
Name: Glen R. Harlow. Title: Small Business Advisor. Email: g.harlow@bayfieldcapitalworks.example. Mobile: (555) 274-3918. Office: (555) 806-2147. www.bayfieldcapitalworks.example

```html
<!DOCTYPE html>
<html lang="en">
<head>
<meta charset="UTF-8">
<title>Bayfield Capital Works – Business Card</title>
<link href="https://fonts.googleapis.com/css2?family=Montserrat:wght@300;400;600&family=Libre+Baskerville:wght@700&display=swap" rel="stylesheet">
<style>
  :root {
    --navy: #1f3566;
    --green: #8cbf26;
    --ink: #3a3d44;
    --card: #ffffff;
    --backdrop: #2b2b2d;
  }
  * { margin: 0; padding: 0; box-sizing: border-box; }
  html, body {
    width: 1200px; height: 688px; overflow: hidden;
    background: var(--backdrop);
    font-family: "Montserrat", sans-serif;
  }
  .canvas { position: relative; width: 1200px; height: 688px; }
  .card {
    position: absolute; top: 190px;
    width: 540px; height: 309px;
    background: var(--card);
    overflow: hidden;
  }
  .card--front { left: 40px; }
  .card--back { left: 620px; }

  .company-name {
    color: var(--navy); font-weight: 600; text-transform: uppercase;
    letter-spacing: 0.02em; white-space: nowrap;
  }
  .tagline {
    color: var(--ink); font-weight: 400;
    letter-spacing: 0.01em; white-space: nowrap;
  }
  .accent-rule {
    width: 60px; height: 3px; background: var(--green);
  }

  /* front */
  .front-lockup {
    position: absolute; left: 0; right: 0; top: 118px;
    text-align: center;
  }
  .front-lockup .company-name { font-size: 22px; }
  .front-lockup .accent-rule { margin: 8px auto 7px; }
  .front-lockup .tagline { font-size: 11px; }
  .brand-square {
    display: inline-block; width: 16px; height: 16px;
    background: var(--navy); margin-right: 10px; vertical-align: -1px;
  }

  /* back */
  .back-mark {
    position: absolute; left: 52px; top: 62px;
    width: 52px; height: 52px; background: var(--navy);
  }
  .contact-rule {
    position: absolute; left: 150px; top: 40px;
    width: 1px; height: 110px; background: var(--navy);
  }
  .contact { position: absolute; left: 168px; top: 36px; }
  .contact-name {
    font-family: "Libre Baskerville", serif; font-weight: 700;
    color: var(--navy); font-size: 17px;
  }
  .contact-title {
    font-size: 11px; font-weight: 400; color: var(--ink); margin-bottom: 10px;
  }
  .contact-list { list-style: none; }
  .contact-list li {
    font-size: 11px; font-weight: 300; color: var(--ink); line-height: 17px;
    white-space: nowrap;
  }
  .contact-label {
    display: inline-block; width: 20px;
    font-family: "Libre Baskerville", serif; font-weight: 700;
    color: var(--navy); font-size: 10px;
  }
  .back-lockup { position: absolute; left: 36px; bottom: 40px; }
  .back-lockup .company-name { font-size: 27px; }
  .back-lockup .accent-rule { margin: 8px 0 7px; }
  .back-lockup .tagline { font-size: 13px; }
</style>
</head>
<body>
<main class="canvas">
  <section class="card card--front" aria-label="Card front">
    <div class="front-lockup">
      <p class="company-name"><span class="brand-square"></span>Bayfield Capital Works, Inc</p>
      <div class="accent-rule"></div>
      <p class="tagline">Trusted guidance for the sale of your main street business</p>
    </div>
  </section>

  <section class="card card--back" aria-label="Card back">
    <div class="back-mark"></div>
    <div class="contact-rule"></div>
    <div class="contact">
      <p class="contact-name">Glen R. Harlow</p>
      <p class="contact-title">Small Business Advisor</p>
      <ul class="contact-list">
        <li><span class="contact-label">M:</span>(555) 274-3918</li>
        <li><span class="contact-label">O:</span>(555) 806-2147</li>
        <li><span class="contact-label">E:</span>g.harlow@bayfieldcapitalworks.example</li>
        <li><span class="contact-label">W:</span>www.bayfieldcapitalworks.example</li>
      </ul>
    </div>
    <div class="back-lockup">
      <p class="company-name">Bayfield Capital Works, Inc</p>
      <div class="accent-rule"></div>
      <p class="tagline">Trusted guidance for the sale of your main street business</p>
    </div>
  </section>
</main>
</body>
</html>
```